VFX Company Business Card Design Project

The Kestrel Works is a decentralized Visual Effects Studio servicing the television and feature film industries.
Project Brief:
Take our logo that was previously designed on Pencil Harbor and make a double sided business card.
Requirements:
- Card MUST be double sided.
- Front of card MUST have the yellow part of our logo against the dark grey background.
- Back of card is completely up to the designer.
- Back of card must include the complete company logo.
Please follow these File Preparation guidelines:
http://printnook.ca/infopage?file=filetype_en&s=PrintNook_new&lang=en
Business

```html
<!DOCTYPE html>
<html lang="en">
<head>
<meta charset="utf-8">
<title>The Kestrel Works – Business Card</title>
<link rel="stylesheet" href="https://fonts.googleapis.com/css2?family=PT+Sans:wght@400;700&display=swap">
<style>
  :root {
    --backdrop: #c9d2d6;
    --card-yellow: #fdc927;
    --card-dark: #343230;
    --ink-dark: #2e2c28;
    --ink-grey: #5a5a5a;
    --rule: #3a3630;
    --brand-yellow: #fdc927;
  }
  * { box-sizing: border-box; margin: 0; padding: 0; }
  html, body {
    width: 1200px; height: 960px; overflow: hidden;
    background: var(--backdrop);
    font-family: "PT Sans", Arial, sans-serif;
  }
  .canvas { position: relative; width: 1200px; height: 960px; }
  .card {
    position: absolute; width: 560px; height: 320px;
    box-shadow: 0 10px 30px rgba(0,0,0,.18);
  }
  /* Contact side */
  .card--contact { left: 90px; top: 110px; background: var(--card-yellow); color: var(--ink-dark); }
  .brand {
    position: absolute; left: 34px; top: 34px;
    display: flex; align-items: center; gap: 14px;
  }
  .brand__dot { width: 34px; height: 34px; border-radius: 50%; background: #fff; }
  .brand__name { font-size: 30px; font-weight: 700; color: var(--ink-grey); letter-spacing: .5px; }
  .person { position: absolute; left: 34px; top: 150px; }
  .person__name { font-size: 28px; font-weight: 400; letter-spacing: .5px; }
  .person__title { font-size: 16px; margin-top: 2px; }
  .divider { position: absolute; left: 34px; right: 34px; top: 222px; border-top: 1.5px solid var(--rule); }
  .contacts {
    position: absolute; left: 34px; top: 238px;
    display: grid; grid-template-columns: 30px auto; row-gap: 4px;
    font-size: 17px; line-height: 1.25;
  }
  .contacts dt { font-size: 15px; }
  .address {
    position: absolute; right: 34px; top: 238px; width: 200px;
    font-size: 14px; line-height: 1.4;
  }
  /* Logo side */
  .card--logo {
    left: 550px; top: 530px; background: var(--card-dark);
    display: flex; align-items: center; justify-content: center; gap: 16px;
  }
  .card--logo .brand__dot { width: 38px; height: 38px; background: var(--brand-yellow); }
  .card--logo .brand__name { color: var(--brand-yellow); font-size: 34px; }
</style>
</head>
<body>
<main class="canvas">
  <section class="card card--contact" aria-label="Card contact side">
    <div class="brand">
      <span class="brand__dot"></span>
      <span class="brand__name">The Kestrel Works</span>
    </div>
    <div class="person">
      <p class="person__name">ALEX MORROW</p>
      <p class="person__title">Managing Partner</p>
    </div>
    <hr class="divider">
    <dl class="contacts">
      <dt>t</dt><dd>(480) 555-0142</dd>
      <dt>e</dt><dd>name@kestrelworks.com</dd>
      <dt>w</dt><dd>www.kestrelworks.com</dd>
    </dl>
    <address class="address">
      4410 North Harbor Lane,<br>Suite 210, Millbrook,<br>Arizona 85999
    </address>
  </section>

  <section class="card card--logo" aria-label="Card logo side">
    <span class="brand__dot"></span>
    <span class="brand__name">The Kestrel Works</span>
  </section>
</main>
</body>
</html>
```